Industrial B2B Company Seeks Complete Redesign

We manufacture solid/liquid filtration equipment for manufacturers of chemicals, pharmaceuticals and mining products. We will be redesigning our website; our current design is outdated, and a more modern look is desired. Navigation can be improved. Call to action on the header, such as "Start Here". Video on home page. Designer should incorporate colors from our logo, at least the blues, the brown/gold is optional. Existing website can be found at www.BrindleSeparators.com. Also, we do not make water filters and references to water or water-like images should be avoided.
Number of Pages Required
1 page
Look and feel
Each slider illustrates characteristics of the customer's brand and the style your logo design should communicate.

```html
<!DOCTYPE html>
<html lang="en">
<head>
<meta charset="utf-8">
<title>Brindle Separators</title>
<link href="https://fonts.googleapis.com/css2?family=Outfit:wght@300;400;500;600;700&family=Oswald:wght@600;700&display=swap" rel="stylesheet">
<style>
:root{
  --navy:#10326b;
  --blue:#1d5aa8;
  --link:#1f63c4;
  --ink:#1d2433;
  --muted:#5b6272;
  --grey:#eef0f3;
  --card:#e8eef6;
  --field:#eceef1;
  --footer:#0d2a55;
  --gold:#f3b21b;
}
*{box-sizing:border-box;margin:0;padding:0}
html,body{width:1200px;height:3588px;overflow:hidden}
body{font-family:"Outfit",sans-serif;color:var(--ink);background:#fff;position:relative}
.abs{position:absolute}
.btn{display:inline-flex;align-items:center;justify-content:center;background:var(--navy);color:#fff;font-weight:500;font-size:15px;border-radius:6px;height:40px;padding:0 22px;white-space:nowrap}
.section-title{font-weight:500;font-size:30px;color:var(--blue);text-align:center;width:100%}

/* nav */
.site-nav{top:0;left:0;width:1200px;height:76px;background:#fff}
.brand{left:120px;top:18px;display:flex;align-items:center;gap:10px;font-weight:700;font-size:20px;color:var(--navy);white-space:nowrap}
.brand-dot{width:18px;height:18px;border-radius:50%;background:var(--blue)}
.nav-links{left:440px;top:28px;display:flex;gap:30px;font-size:13px;color:var(--ink);white-space:nowrap}
.nav-links .active{color:var(--link);font-weight:600}
.nav-cta{left:935px;top:16px;height:44px;font-size:14px;padding:0 24px}

/* hero */
.hero{top:76px;left:0;width:1200px;height:414px;background:linear-gradient(90deg,#cfe3f8 0%,#e3eefb 45%,#d7e8fa 100%)}
.hero-media{left:560px;top:60px;width:590px;height:330px;border-radius:10px;background:linear-gradient(135deg,#6b8fb8,#2f5f9c 55%,#8fb0d4)}
.hero-title{left:120px;top:132px;font-family:"Oswald",sans-serif;font-weight:700;font-size:48px;color:var(--navy);letter-spacing:.5px;line-height:1;white-space:nowrap}
.hero-sub{left:122px;top:196px;font-size:19px;font-weight:500;color:var(--navy)}
.hero-btn{left:122px;top:250px;height:40px;font-size:13px}

/* products */
.products-title{top:620px;left:0}
.product-grid{top:712px;left:140px;display:flex;gap:26px}
.product-card{width:208px;height:252px;background:#fff;border-radius:8px;box-shadow:0 4px 18px rgba(20,40,80,.12);padding:12px}
.product-media{height:170px;border-radius:6px;background:linear-gradient(160deg,#dfe3e8,#9aa3ad)}
.product-name{margin-top:14px;font-weight:600;font-size:15px}
.product-link{margin-top:6px;font-size:13px;color:var(--link);font-weight:500}
.view-all{top:1004px;left:542px;height:38px;font-size:13px;border-radius:20px;background:#4e86c8}

/* about */
.about-media{top:1118px;left:150px;width:330px;height:330px;border-radius:50%;background:radial-gradient(circle at 40% 45%,#c9d3de,#3a6ea9 60%,#0f2f5c)}
.about-title{top:1128px;left:610px;font-size:30px;font-weight:600;color:var(--blue)}
.about-text{top:1200px;left:610px;width:450px;font-size:12.5px;line-height:1.6;color:var(--muted)}
.about-text p+p{margin-top:16px}
.about-btn{top:1464px;left:610px;height:38px;font-size:13px}

/* services */
.services{top:1636px;left:0;width:1200px;height:432px;background:var(--grey)}
.services-title{top:56px;left:0}
.service-row{top:136px;left:160px;display:flex;gap:70px}
.service{width:240px;text-align:center}
.service-icon{width:84px;height:84px;border-radius:50%;background:var(--navy);margin:0 auto;display:flex;align-items:center;justify-content:center}
.service-name{margin-top:18px;font-weight:600;font-size:16px}
.service-text{margin-top:10px;font-size:11.5px;line-height:1.5;color:var(--muted)}
.service-link{margin-top:10px;font-size:12px;color:var(--link);font-weight:500}

/* testimonials */
.reviews-title{top:2148px;left:0}
.review-card{width:432px;height:200px;background:var(--card);border-radius:12px;padding:58px 26px 0}
.review-card p{font-size:14px;line-height:1.55;color:var(--ink)}
.quote-badge{width:40px;height:40px;background:var(--navy);border-radius:8px;top:-14px;left:24px;display:flex;align-items:center;justify-content:center}
.arrow{width:34px;height:34px;border-radius:50%;background:var(--navy);display:flex;align-items:center;justify-content:center}
.reviewer{display:flex;align-items:center;gap:14px}
.avatar{width:60px;height:60px;border-radius:50%;background:linear-gradient(135deg,#d9b9a0,#6b4a3a)}
.stars{display:flex;gap:3px}
.reviewer-name{font-weight:600;font-size:16px;margin-top:4px}

/* contact */
.contact-media{top:2668px;left:140px;width:396px;height:384px;border-radius:16px;background:linear-gradient(160deg,#3f6f9f,#16365e 60%,#0b1d38)}
.contact-info{top:2830px;left:168px;color:#fff;font-size:13px;line-height:1.4}
.info-row{display:flex;gap:12px;margin-bottom:14px}
.info-row b{display:block;font-weight:600}
.contact-title{top:2690px;left:610px;font-size:30px;font-weight:600;color:var(--blue)}
.form{top:2770px;left:610px;width:450px}
.field{background:var(--field);height:38px;border-radius:4px;font-size:12px;color:#8a909b;padding:11px 12px}
.form-row{display:flex;gap:14px;margin-bottom:14px}
.form-row .field{flex:1}
.textarea{height:96px}
.submit{margin-top:14px;height:40px;font-size:13px}

/* footer */
.footer{top:3100px;left:0;width:1200px;height:488px}
.footer-brand{top:270px;left:120px;font-weight:700;font-size:22px;color:#fff;display:flex;align-items:center;gap:10px;white-space:nowrap}
.footer-col{top:210px;color:#fff}
.footer-col h4{font-weight:600;font-size:15px;margin-bottom:14px}
.footer-col li{list-style:none;font-size:12px;line-height:2;color:#d5deec}
.sub-input{width:206px;height:36px;border:1px solid #9fb2cf;border-radius:20px;font-size:12px;color:#c7d2e4;padding:10px 16px}
.sub-btn{margin-top:12px;width:206px;height:36px;border-radius:20px;background:#fff;color:var(--navy);font-weight:600;font-size:13px;display:flex;align-items:center;justify-content:center}
.footer-rule{top:420px;left:120px;width:960px;height:1px;background:#3d5a85}
.copyright{top:444px;left:120px;font-size:12px;color:#c7d2e4}
.socials{top:436px;left:930px;display:flex;gap:10px}
.socials span{width:26px;height:26px;border-radius:50%;background:#fff}
</style>
</head>
<body>

<header class="site-nav abs">
  <div class="brand abs"><span class="brand-dot"></span>Brindle Separators</div>
  <nav class="nav-links abs"><span class="active">Home</span><span>About Us</span><span>Our Products</span><span>Industries Served</span><span>Resources</span></nav>
  <span class="btn nav-cta abs">Contact Us</span>
</header>

<section class="hero abs">
  <div class="hero-media abs" role="img" aria-label="Large industrial filter press unit with blue frame"></div>
  <h1 class="hero-title abs">BRINDLE SEPARATORS</h1>
  <p class="hero-sub abs">Optimizing Industrial Filtration Processes</p>
  <span class="btn hero-btn abs">Start Here</span>
</section>

<h2 class="section-title products-title abs">Our Products</h2>
<div class="product-grid abs">
  <div class="product-card"><div class="product-media" role="img" aria-label="Nutsche filter vessel"></div><div class="product-name">Nutsche Filters</div><div class="product-link">View Product →</div></div>
  <div class="product-card"><div class="product-media" role="img" aria-label="Twin disc filter housing"></div><div class="product-name">TR Twin Disc Filter</div><div class="product-link">View Product →</div></div>
  <div class="product-card"><div class="product-media" role="img" aria-label="Vertical filter unit"></div><div class="product-name">Vertical Filters</div><div class="product-link">View Product →</div></div>
  <div class="product-card"><div class="product-media" role="img" aria-label="Laboratory filter on stand"></div><div class="product-name">Laboratory Filter</div><div class="product-link">View Product →</div></div>
</div>
<span class="btn view-all abs">View All</span>

<div class="about-media abs" role="img" aria-label="Stainless filtration equipment in a plant"></div>
<h2 class="about-title abs">About Brindle Separators</h2>
<div class="about-text abs">
  <p>At Brindle Separators, we've been setting the standard in liquid filtration for nearly a century. As a leading manufacturer, we pride ourselves on crafting high-quality, long-lasting filtration equipment tailored to meet the unique needs of our customers. With each of our products we pair it with unwavering reliability, predictability, superior service and exceptional returns on your investment that your decades.</p>
  <p>Our legacy is one of innovation. Almost a century ago, Brindle Separators pioneered the first modern style horizontal plate filter, introduced the first residential and field-use filters, and even revolutionized the cooking oil filtration process.</p>
</div>
<span class="btn about-btn abs">Learn More</span>

<section class="services abs">
  <h2 class="section-title services-title abs">Our Services</h2>
  <div class="service-row abs">
    <div class="service">
      <div class="service-icon"><svg width="40" height="40" viewBox="0 0 40 40" fill="none" stroke="#fff" stroke-width="2"><path d="M6 8h28L23 22v10l-6 3V22z"/></svg></div>
      <div class="service-name">Filter Media</div>
      <div class="service-text">As an ISO qualified supplier we hold the highest standards for each sourced component that goes into our products.</div>
      <div class="service-link">Learn More →</div>
    </div>
    <div class="service">
      <div class="service-icon"><svg width="40" height="40" viewBox="0 0 40 40" fill="none" stroke="#fff" stroke-width="2"><circle cx="20" cy="20" r="6"/><circle cx="20" cy="20" r="13"/><path d="M20 4v4M20 32v4M4 20h4M32 20h4"/></svg></div>
      <div class="service-name">Process Consulting</div>
      <div class="service-text">Our experience and filtration knowledge can be put to work in your process. Share your goals and we will guide the next steps.</div>
      <div class="service-link">Learn More →</div>
    </div>
    <div class="service">
      <div class="service-icon"><svg width="40" height="40" viewBox="0 0 40 40" fill="none" stroke="#fff" stroke-width="2"><rect x="11" y="6" width="18" height="28" rx="3"/><path d="M11 14h18M11 22h18"/></svg></div>
      <div class="service-name">Rental Filters</div>
      <div class="service-text">We stock a complete fleet of rental filters ready to ship now. Whatever your need, our team can help you.</div>
      <div class="service-link">Learn More →</div>
    </div>
  </div>
</section>

<h2 class="section-title reviews-title abs">Our Happy Customers</h2>
<div class="arrow abs" style="top:2360px;left:118px"><svg width="14" height="14" viewBox="0 0 14 14"><path d="M9 2L4 7l5 5" stroke="#fff" stroke-width="2" fill="none"/></svg></div>
<div class="arrow abs" style="top:2360px;left:1048px"><svg width="14" height="14" viewBox="0 0 14 14"><path d="M5 2l5 5-5 5" stroke="#fff" stroke-width="2" fill="none"/></svg></div>
<div class="review-card abs" style="top:2276px;left:140px">
  <div class="quote-badge abs"><svg width="18" height="14" viewBox="0 0 18 14" fill="#fff"><path d="M0 14V7L4 0h3L5 6h3v8zM10 14V7l4-7h3l-2 6h3v8z"/></svg></div>
  <p>A technically excellent Pilates training! Each training session includes new exercise sequences with precise instructions, and different small equipment is often used. My summary, definitely try it out, highly recommended. Thanks Yvonne!</p>
</div>
<div class="review-card abs" style="top:2276px;left:610px">
  <div class="quote-badge abs"><svg width="18" height="14" viewBox="0 0 18 14" fill="#fff"><path d="M0 14V7L4 0h3L5 6h3v8zM10 14V7l4-7h3l-2 6h3v8z"/></svg></div>
  <p>A technically excellent Pilates training! Each training session includes new exercise sequences with precise instructions, and different small equipment is often used. My summary, definitely try it out, highly recommended. Thanks Yvonne!</p>
</div>
<div class="reviewer abs" style="top:2508px;left:210px">
  <div class="avatar" role="img" aria-label="Customer portrait"></div>
  <div><div class="stars"><svg width="90" height="16" viewBox="0 0 90 16" fill="#f3b21b"><g id="s"><path d="M8 0l2.4 5 5.6.7-4 3.8 1 5.5L8 12.4 3 15l1-5.5-4-3.8L5.6 5z"/></g><use href="#s" x="18"/><use href="#s" x="36"/><use href="#s" x="54"/><use href="#s" x="72"/></svg></div><div class="reviewer-name">Dale Harmon</div></div>
</div>
<div class="reviewer abs" style="top:2508px;left:676px">
  <div class="avatar" role="img" aria-label="Customer portrait"></div>
  <div><div class="stars"><svg width="90" height="16" viewBox="0 0 90 16" fill="#f3b21b"><use href="#s"/><use href="#s" x="18"/><use href="#s" x="36"/><use href="#s" x="54"/><use href="#s" x="72"/></svg></div><div class="reviewer-name">Owen Castell</div></div>
</div>

<div class="contact-media abs" role="img" aria-label="Industrial plant interior with piping"></div>
<div class="contact-info abs">
  <div class="info-row"><svg width="16" height="18" viewBox="0 0 16 18" fill="#fff"><path d="M8 0a6 6 0 0 1 6 6c0 4.5-6 12-6 12S2 10.5 2 6a6 6 0 0 1 6-6zm0 4a2 2 0 1 0 0 4 2 2 0 0 0 0-4z"/></svg><span>48 Harlow Road, Millbrook,<br>TX 70000 USA</span></div>
  <div class="info-row"><svg width="16" height="14" viewBox="0 0 16 14" fill="none" stroke="#fff" stroke-width="1.6"><rect x="1" y="1" width="14" height="12" rx="1"/><path d="M1 2l7 6 7-6"/></svg><span><b>Email</b>sales@brindleseparators.com</span></div>
  <div class="info-row"><svg width="16" height="16" viewBox="0 0 16 16" fill="#fff"><path d="M3 0l3 4-2 2c1 2 3 4 6 6l2-2 4 3-2 3C7 16 0 9 0 2z"/></svg><span><b>Phone</b>(555) 210-4471</span></div>
  <div class="info-row"><svg width="16" height="16" viewBox="0 0 16 16" fill="none" stroke="#fff" stroke-width="1.6"><rect x="1" y="5" width="14" height="8" rx="1"/><path d="M4 5V1h8v4M4 13v2h8v-2"/></svg><span><b>Fax</b>(555) 210-1165</span></div>
</div>
<h2 class="contact-title abs">Contact Us</h2>
<div class="form abs">
  <div class="form-row"><div class="field">Name</div><div class="field">Email</div></div>
  <div class="form-row"><div class="field">Phone</div><div class="field">Subject</div></div>
  <div class="form-row"><div class="field">Address</div></div>
  <div class="field textarea">How can we help solve your separation needs?</div>
  <span class="btn submit">Submit Now</span>
</div>

<footer class="footer abs">
  <svg class="abs" style="top:0;left:0" width="1200" height="488" viewBox="0 0 1200 488"><path d="M0 60C300 0 700 0 1200 40V488H0z" fill="#0d2a55"/></svg>
  <div class="footer-brand abs"><span class="brand-dot"></span>Brindle Separators</div>
  <div class="footer-col abs" style="left:476px"><h4>Quick Links</h4><ul><li>Home</li><li>About Us</li><li>Services</li><li>Products</li></ul></div>
  <div class="footer-col abs" style="left:654px"><h4>Resources</h4><ul><li>Privacy Policy</li><li>Terms Of Service</li><li>Contact Us</li></ul></div>
  <div class="footer-col abs" style="left:852px"><h4>Subscribe</h4><div class="sub-input">Enter your email</div><div class="sub-btn">Subscribe</div></div>
  <div class="footer-rule abs"></div>
  <div class="copyright abs">© 2024 Brindle Separators Inc. All rights reserved.</div>
  <div class="socials abs"><span></span><span></span><span></span><span></span></div>
</footer>

</body>
</html>
```